BrivoTerna. Lantern of the Steady Harvest. Business card

Professional business card for BrivoTerna (Lantern of the Steady Harvest)
My rationale: Strategy-> Execution-> Results-> Value that lead to the BrivoTerna name: We put the Lantern of the Steady Harvest.
We deliver value to our customers helping them at defining a good strategy (cyan arrow). 90% of well formulated strategies fail due to poor execution so we also consider strategical execution very important (green arrow). Due to the execution we obtain the results (blue arrow). Finally, the results provide feedback to redefine strategy, and the new strategy has to be executed and new results obtained providing new feedback and on and on. It's like a wheel that finally, must create corporate value: value for shareholders, staholders, employees, providers...-

Target Market(s)

CEOs and steering comitees , invewrnent funds

Industry/Entity Type

Business Consultant

Contact Information for Business Card

Teodoro Vinsquel
CEO & Founder
teodoro.vinsquel@brivoterna-example.com
Mobile: +34 655.803.912
www.brivoterna-example.com

Colors

Designer to choose colors to be used in the design.

Requirements
Nice to have
• Nice to hace the words: Strategy, execution, results
• Nice to vave the claim: Lantern of the Steady Harvest
• The three colors should be shown:
• cyan for STRATEGY
• green for EXECUTION
• blue for RESULTS
Should not have
• Complete black background

```html
<!DOCTYPE html>
<html lang="en">
<head>
<meta charset="utf-8">
<title>BrivoTerna – Business Card</title>
<link rel="stylesheet" href="https://fonts.googleapis.com/css2?family=Roboto+Condensed:wght@400;700&display=swap">
<style>
  :root {
    --backdrop: #d8ccb8;
    --card-white: #ffffff;
    --brand-cyan: #2a9fdc;
    --brand-blue: #223f94;
    --brand-green: #97c93d;
    --ink-navy: #22338c;
    --ink-dark: #2b2b2b;
  }
  * { margin: 0; padding: 0; box-sizing: border-box; }
  html, body {
    width: 1200px; height: 900px; overflow: hidden;
    background: var(--backdrop);
    font-family: "Roboto Condensed", "Arial Narrow", sans-serif;
  }
  .canvas { position: relative; width: 1200px; height: 900px; }

  .card {
    position: absolute; left: 311px; width: 577px; height: 329px;
    overflow: hidden;
  }

  /* Front */
  .card--front {
    top: 98px;
    background: linear-gradient(200deg, var(--brand-blue) 0%, #2a6bb5 50%, var(--brand-cyan) 100%);
    color: var(--card-white);
    text-align: center;
  }
  .front__name {
    position: absolute; left: 0; right: 0; top: 176px;
    font-size: 50px; font-weight: 700; letter-spacing: -0.5px; line-height: 1;
  }
  .front__claim {
    position: absolute; left: 0; right: 0; top: 231px;
    font-size: 17px; font-weight: 400; letter-spacing: 0.4px; text-transform: uppercase;
  }
  .front__pillars {
    position: absolute; left: 0; right: 0; bottom: 0; height: 39px;
    background: var(--brand-green);
    display: flex; align-items: center; justify-content: center;
    font-size: 15px; letter-spacing: 0.4px; text-transform: uppercase;
  }
  .front__pillars .sep { margin: 0 8px; }

  /* Back */
  .card--back {
    top: 472px;
    background: var(--card-white);
    color: var(--ink-dark);
  }
  .back__name {
    position: absolute; left: 31px; top: 36px;
    font-size: 48px; font-weight: 700; color: var(--ink-navy);
    letter-spacing: -0.5px; line-height: 1;
  }
  .person { position: absolute; left: 31px; top: 149px; }
  .person__name {
    font-size: 17px; font-weight: 700; color: var(--ink-navy);
    text-transform: uppercase; letter-spacing: 0.3px;
  }
  .person__role { font-size: 12.5px; text-transform: uppercase; margin-top: 2px; }

  .contacts { position: absolute; left: 31px; top: 226px; list-style: none; }
  .contacts li {
    display: flex; align-items: center; gap: 7px;
    font-size: 15px; height: 24.5px;
  }
  .contacts svg { width: 17px; height: 17px; fill: var(--ink-navy); flex: none; }
</style>
</head>
<body>
<div class="canvas">

  <section class="card card--front" aria-label="Card front">
    <div class="front__name">BrivoTerna</div>
    <div class="front__claim">Lantern of the Steady Harvest</div>
    <div class="front__pillars">
      <span>Strategy</span><span class="sep">|</span><span>Execution</span><span class="sep">|</span><span>Results</span>
    </div>
  </section>

  <section class="card card--back" aria-label="Card back">
    <div class="back__name">BrivoTerna</div>

    <div class="person">
      <div class="person__name">Teodoro Vinsquel</div>
      <div class="person__role">CEO &amp; Founder</div>
    </div>

    <ul class="contacts">
      <li>
        <svg viewBox="0 0 16 16" aria-hidden="true"><path d="M4 0h8a1.5 1.5 0 0 1 1.5 1.5v13A1.5 1.5 0 0 1 12 16H4a1.5 1.5 0 0 1-1.5-1.5v-13A1.5 1.5 0 0 1 4 0zm0 2v10.5h8V2zm4 11.2a.9.9 0 1 0 0 1.8.9.9 0 0 0 0-1.8z"/></svg>
        <span>+34 655 803 912</span>
      </li>
      <li>
        <svg viewBox="0 0 16 16" aria-hidden="true"><path d="M0 3h16v1.2L8 9 0 4.2z"/><path d="M0 5.8l8 4.8 8-4.8V13H0z"/></svg>
        <span>teodoro.vinsquel@brivoterna-example.com</span>
      </li>
      <li>
        <svg viewBox="0 0 16 16" aria-hidden="true"><path d="M8 0a8 8 0 1 0 0 16A8 8 0 0 0 8 0zm0 1.5c.9 0 1.9 1.6 2.3 4H5.7C6.1 3.1 7.1 1.5 8 1.5zM5.5 7h5a12 12 0 0 1 0 2h-5a12 12 0 0 1 0-2zM1.6 7H4a14 14 0 0 0 0 2H1.6a6.5 6.5 0 0 1 0-2zm10.4 0h2.4a6.5 6.5 0 0 1 0 2H12a14 14 0 0 0 0-2zM5.7 10.5h4.6c-.4 2.4-1.4 4-2.3 4s-1.9-1.6-2.3-4z"/></svg>
        <span>www.brivoterna-example.com</span>
      </li>
    </ul>
  </section>

</div>
</body>
</html>
```